UX - Need some screens design for a Skill Assessment Application

I am building an app to carry out skill assessments. Depending on how the assessment is configured, it may have one or more parts
1. Question based assessment (Multiple Choice, True False, Fill in the blanks"
2. Endorsement by two colleagues - A screen that allows user to pick colleagues based on search and shows the status of pending requests
3. A written submission - a page that explains the format of the submission and a file upload
As each assessment can be configured with or without any of the steps, the assessment UI must be such that these areas get hidden/displayed based on configuration.
Colour codes to be used can be #0e78bb and #ffffff
There will also be a start screen (instructions) and an end screen (results)
Target Market(s)
Enterprise software
Number of Pages Required
4 page

```html
<!DOCTYPE html>
<html lang="en">
<head>
<meta charset="utf-8">
<title>Application Design Capabilities – Endorsement</title>
<link href="https://fonts.googleapis.com/css2?family=Inter:wght@400;500;600;700&display=swap" rel="stylesheet">
<style>
:root{
  --nav:#0a56a8;
  --brand:#0e78bb;
  --white:#ffffff;
  --ink:#222a33;
  --text:#3b4148;
  --muted:#5f656c;
  --line:#dfe3e7;
  --band:#f2f3f5;
  --page:#f5f6f7;
  --head:#e7f3fb;
  --chip:#eff0f1;
}
*{box-sizing:border-box;margin:0;padding:0}
html,body{width:1200px;height:686px;overflow:hidden}
body{font-family:"Inter",Arial,sans-serif;background:var(--page);color:var(--text);position:relative}

.topbar{height:43px;background:var(--nav);display:flex;align-items:center;padding:0 57px;color:var(--white)}
.brand{display:flex;align-items:center;gap:14px;font-size:14.5px;font-weight:600}
.brand-dot{width:20px;height:20px;border-radius:50%;background:var(--white)}
.mainnav{margin-left:auto;display:flex;align-items:center;gap:20px;font-size:12px}
.mainnav a{color:rgba(255,255,255,.82);text-decoration:none}
.mainnav a.active{color:var(--white);font-weight:600}
.user{display:flex;align-items:center;gap:6px}
.user-photo{width:27px;height:27px;border-radius:50%;background:linear-gradient(135deg,#5a4a52,#c9a99b)}

.pagehead{background:var(--white);height:97px;position:relative}
.crumbs{position:absolute;left:57px;top:65px;transform:translateY(-50%);display:flex;align-items:center;font-size:11.5px;color:var(--muted)}
.pagehead .crumbs{top:9px;transform:none;height:28px;margin-top:0}
.crumbs a{color:var(--brand);text-decoration:none}
.crumbs .sep{margin:0 7px;color:var(--muted)}
.crumbs svg{margin-right:12px}
.title{position:absolute;left:88px;top:56px;display:flex;align-items:center;gap:13px;font-size:21px;font-weight:600;color:var(--ink)}

.filters{height:77px;background:var(--band);border-top:1px solid var(--line);border-bottom:1px solid var(--line);position:relative}
.field{position:absolute;top:14px}
.field label{display:block;font-size:9.5px;color:var(--text);margin-bottom:6px}
.control{height:31px;background:var(--white);border:1px solid #d6dade;border-radius:3px;display:flex;align-items:center;justify-content:space-between;padding:0 12px 0 13px;font-size:11.5px;color:var(--ink)}
.control.search{color:#9aa0a6}
.send-link{position:absolute;right:88px;top:39px;font-size:11px;color:var(--brand)}

.card{position:absolute;left:88px;top:238px;width:1024px;height:413px;background:var(--white);border:1px solid var(--line);border-radius:4px;overflow:hidden}
.row{display:grid;grid-template-columns:18px 192px 356px 193px 1fr auto;align-items:center;padding:0 18px 0 16px;height:45.4px;border-bottom:1px solid var(--line)}
.row.header{height:43px;background:var(--head);font-size:12px;font-weight:500;color:var(--text)}
.box{width:14px;height:14px;border:1px solid #cdd2d7;border-radius:2px;background:var(--white);display:flex;align-items:center;justify-content:center}
.box.checked{background:var(--brand);border-color:var(--brand)}
.person{display:flex;align-items:center;gap:11px;font-size:12.5px;color:var(--ink);padding-left:6px}
.avatar{width:27px;height:27px;border-radius:50%;flex:none}
.skills{display:flex;gap:4px;padding-left:6px}
.header .skills{font-size:12px}
.chip{font-size:9.5px;background:var(--chip);border-radius:10px;padding:3px 7px;color:var(--muted)}
.role{font-size:10.5px;color:var(--muted);padding-left:6px}
.header .role{font-size:12px;color:var(--text)}
.company{font-size:10.5px;color:var(--brand);font-weight:500;padding-left:6px}
.header .company{font-size:12px;color:var(--text);font-weight:500}
.btn{height:30px;border-radius:3px;font-size:11.5px;display:flex;align-items:center;justify-content:center;font-family:inherit}
.btn.add{width:49px;border:1px solid var(--brand);color:var(--brand);background:var(--white)}
.btn.cancel{width:64px;background:var(--brand);color:var(--white);border:1px solid var(--brand)}

.pager{position:absolute;left:0;right:0;bottom:0;height:52px;display:flex;align-items:center;justify-content:center;font-size:12px}
.pager .nav-btn{width:63px;height:30px;border:1px solid #dfe2e5;border-radius:3px;color:#c3c7cb;display:flex;align-items:center;justify-content:center;gap:4px;font-size:11px}
.pager .page{width:31px;height:31px;display:flex;align-items:center;justify-content:center;color:var(--muted)}
.pager .page.current{background:var(--brand);color:var(--white);border-radius:2px;margin-left:14px}
.pager .page.next{margin-right:18px;margin-left:3px}
</style>
</head>
<body>

<header class="topbar">
  <div class="brand"><span class="brand-dot"></span>LogoPlaceholder</div>
  <nav class="mainnav">
    <a href="#">Assessments</a>
    <a href="#" class="active">Endorsement</a>
    <a href="#">Submissions</a>
    <a href="#">Results</a>
    <span class="user">
      <span class="user-photo" role="img" aria-label="User profile photo"></span>
      <svg width="10" height="6" viewBox="0 0 10 6"><path d="M1 1l4 4 4-4" fill="none" stroke="#fff" stroke-width="1.5"/></svg>
    </span>
  </nav>
</header>

<section class="pagehead">
  <div class="crumbs" style="top:60px"></div>
  <div class="crumbs">
    <svg width="19" height="19" viewBox="0 0 19 19"><circle cx="9.5" cy="9.5" r="8.5" fill="none" stroke="#0e78bb" stroke-width="1.6"/><path d="M13.5 9.5H6M9 6.2L5.7 9.5 9 12.8" fill="none" stroke="#0e78bb" stroke-width="1.6" stroke-linecap="round" stroke-linejoin="round"/></svg>
    <a href="#">Endorsement</a><span class="sep">/</span><a href="#">New Endorsement Request</a><span class="sep">/</span><span>Application Design Capabilities</span>
  </div>
  <h1 class="title">
    <svg width="22" height="20" viewBox="0 0 22 20" fill="none" stroke="#555b61" stroke-width="1.4"><circle cx="11" cy="6.5" r="3"/><circle cx="4.5" cy="4" r="2.2"/><circle cx="17.5" cy="4" r="2.2"/><path d="M5 18c0-3.5 2.7-6 6-6s6 2.5 6 6"/><path d="M1 13c0-2.5 1.5-4.3 3.5-4.3M21 13c0-2.5-1.5-4.3-3.5-4.3"/></svg>
    Application Design Capabilities
  </h1>
</section>

<section class="filters">
  <div class="field" style="left:88px;width:300px">
    <label>Choose Category</label>
    <div class="control">Application Design Capabilities (24)<svg width="10" height="6" viewBox="0 0 10 6"><path d="M1 1l4 4 4-4" fill="none" stroke="#333" stroke-width="1.3"/></svg></div>
  </div>
  <div class="field" style="left:402px;width:171px">
    <label>Effective Date</label>
    <div class="control">Select date<svg width="10" height="6" viewBox="0 0 10 6"><path d="M1 1l4 4 4-4" fill="none" stroke="#333" stroke-width="1.3"/></svg></div>
  </div>
  <div class="field" style="left:587px;width:286px">
    <label>Endorsement</label>
    <div class="control search">Search<svg width="15" height="15" viewBox="0 0 15 15"><circle cx="6.5" cy="6.5" r="5" fill="none" stroke="#777" stroke-width="1.3"/><path d="M10.2 10.2L14 14" stroke="#777" stroke-width="1.3"/></svg></div>
  </div>
  <a class="send-link">Send Endorsement Request</a>
</section>

<main class="card">
  <div class="row header">
    <span class="box"></span><span class="person">Endorsements</span><span class="skills">Skill &amp; Expertise</span><span class="role">Role</span><span class="company">Company</span><span></span>
  </div>

  <div class="row">
    <span class="box"></span>
    <span class="person"><span class="avatar" role="img" aria-label="Photo of Mei Lin Zhao" style="background:linear-gradient(135deg,#6b4a2e,#d7b08a)"></span>Mei Lin Zhao</span>
    <span class="skills"><span class="chip">UI</span><span class="chip">UX</span><span class="chip">Wireframe</span><span class="chip">Concept Design</span><span class="chip">Framewise</span></span>
    <span class="role">Linhe Industries Ltd.</span><span class="company">Linhe Industries Ltd.</span>
    <button class="btn add">Add</button>
  </div>

  <div class="row">
    <span class="box"></span>
    <span class="person"><span class="avatar" role="img" aria-label="Photo of Owen Harker" style="background:linear-gradient(135deg,#2b2b2b,#8a7a6c)"></span>Owen Harker</span>
    <span class="skills"><span class="chip">Concept Design</span><span class="chip">Framewise</span></span>
    <span class="role">Brightfold Corp.</span><span class="company">Brightfold Corp.</span>
    <button class="btn cancel">Cancel</button>
  </div>

  <div class="row">
    <span class="box"></span>
    <span class="person"><span class="avatar" role="img" aria-label="Photo of Lucas Brenner" style="background:linear-gradient(135deg,#3d3d3d,#b9a89a)"></span>Lucas Brenner</span>
    <span class="skills"><span class="chip">UI</span><span class="chip">Design Analytic</span></span>
    <span class="role">Brightfold Corp.</span><span class="company">Brightfold Corp.</span>
    <button class="btn add">Add</button>
  </div>

  <div class="row">
    <span class="box checked"><svg width="10" height="8" viewBox="0 0 10 8"><path d="M1 4l3 3 5-6" fill="none" stroke="#fff" stroke-width="1.7"/></svg></span>
    <span class="person"><span class="avatar" role="img" aria-label="Photo of Nadia Rowe" style="background:linear-gradient(135deg,#e2b77a,#f3d9c4)"></span>Nadia Rowe</span>
    <span class="skills"><span class="chip">Wireframe</span><span class="chip">Concept Design</span><span class="chip">Framewise</span></span>
    <span class="role">Brightfold Corp.</span><span class="company">Brightfold Corp.</span>
    <button class="btn add">Add</button>
  </div>

  <div class="row">
    <span class="box"></span>
    <span class="person"><span class="avatar" role="img" aria-label="Photo of Daniel Ross Jr." style="background:linear-gradient(135deg,#9ccbe0,#8a5d45)"></span>Daniel Ross Jr.</span>
    <span class="skills"><span class="chip">UX</span><span class="chip">Concept Design</span></span>
    <span class="role">Brightfold Corp.</span><span class="company">Brightfold Corp.</span>
    <button class="btn add">Add</button>
  </div>

  <div class="row">
    <span class="box checked"><svg width="10" height="8" viewBox="0 0 10 8"><path d="M1 4l3 3 5-6" fill="none" stroke="#fff" stroke-width="1.7"/></svg></span>
    <span class="person"><span class="avatar" role="img" aria-label="Photo of Sari W. Kusuma" style="background:linear-gradient(135deg,#2d3550,#c7a192)"></span>Sari W. Kusuma</span>
    <span class="skills"><span class="chip">Design Analytic</span><span class="chip">Wireframe</span></span>
    <span class="role">Arunda Studio</span><span class="company">Arunda Studio</span>
    <button class="btn add">Add</button>
  </div>

  <div class="row">
    <span class="box"></span>
    <span class="person"><span class="avatar" role="img" aria-label="Photo of Peter Vale" style="background:linear-gradient(135deg,#d8d8d8,#6e5444)"></span>Peter Vale</span>
    <span class="skills"><span class="chip">Wireframe</span><span class="chip">UX</span><span class="chip">Concept Design</span><span class="chip">UI</span></span>
    <span class="role">Brightfold Corp.</span><span class="company">Brightfold Corp.</span>
    <button class="btn add">Add</button>
  </div>

  <div class="pager">
    <span class="nav-btn"><svg width="5" height="8" viewBox="0 0 5 8"><path d="M4 1L1 4l3 3" fill="none" stroke="#c3c7cb" stroke-width="1.2"/></svg>Back</span>
    <span class="page current">1</span>
    <span class="page next">2</span>
    <span class="nav-btn">Next<svg width="5" height="8" viewBox="0 0 5 8"><path d="M1 1l3 3-3 3" fill="none" stroke="#c3c7cb" stroke-width="1.2"/></svg></span>
  </div>
</main>

</body>
</html>
```